Corvane Business Cards

Front of business card will have logo, name, address, & telephone number. Back of card will have a list of services provided - Roads, Substation Pads, Temporary Pads, Site Pads, Land Leveling, Powerline Row Cleaning, Land Clearing, Gates, Fencing, Construction Entrances, Excavation, Trenching, Underground Utilities, Directional Boring, Pile Driving. We are a construction company that uses heavy equipment like bulldozers, motor graders/blades, dump trucks, backhoes, hydro axes, & skid loaders. We build roads, pads, & install electric utility lines & waterlines underground. This logo is new. The word "Construction" can be smaller as uploaded 2 example edited logos. We will be using this card design for many employees.
Target Market(s)
Industrial Electric Powerline, Wind Turbine, Solar Panel, & Water Utility companies.
Contact Information for Business Card
Name/Position - Dwayne Halster - Owner
Address: 4875 FM 309
Ardell, NM 87412
Phone number - (505) 482-5096

```html
<!DOCTYPE html>
<html lang="en">
<head>
<meta charset="utf-8">
<title>Corvane Construction – Business Card</title>
<link rel="stylesheet" href="https://fonts.googleapis.com/css2?family=Alegreya+Sans:wght@400;500;700&family=Marcellus&display=swap">
<style>
  :root {
    --page-bg: #e9e6e2;
    --card-frost: #f1efee;
    --card-maroon: #5a1d26;
    --card-maroon-deep: #4a1720;
    --text-light: #f4eeee;
    --text-soft: #e6dadb;
    --brand-ink: #5a1d26;
  }
  * { margin: 0; padding: 0; box-sizing: border-box; }
  html, body {
    width: 1200px;
    height: 969px;
    overflow: hidden;
    background: var(--page-bg);
  }
  .canvas {
    position: relative;
    width: 1200px;
    height: 969px;
  }
  .business-card {
    position: absolute;
    left: 130px;
    top: 216px;
    width: 940px;
    height: 537px;
    border-radius: 26px;
    overflow: hidden;
    background: var(--card-frost);
    box-shadow: 0 18px 40px rgba(60, 30, 30, 0.18);
    font-family: "Alegreya Sans", "Optima", sans-serif;
  }
  .card-art {
    position: absolute;
    inset: 0;
    width: 100%;
    height: 100%;
  }
  .brand-name {
    position: absolute;
    left: 99px;
    top: 188px;
    color: var(--brand-ink);
    font-family: "Marcellus", "Optima", sans-serif;
    line-height: 1;
  }
  .brand-name .brand-main {
    display: block;
    font-size: 62px;
    letter-spacing: 2px;
  }
  .brand-name .brand-sub {
    display: block;
    margin-top: 70px;
    font-size: 34px;
    letter-spacing: 0.5px;
  }
  .holder {
    position: absolute;
    right: 60px;
    top: 64px;
    text-align: right;
    color: var(--text-light);
    line-height: 1.1;
  }
  .holder-name {
    font-size: 30px;
    font-weight: 700;
    letter-spacing: 1px;
  }
  .holder-role {
    margin-top: 2px;
    font-size: 20px;
    font-weight: 500;
    color: var(--text-soft);
  }
  .contact {
    position: absolute;
    right: 60px;
    bottom: 48px;
    text-align: right;
    color: var(--text-soft);
    font-size: 21px;
    font-weight: 500;
    line-height: 1.25;
    font-style: normal;
  }
</style>
</head>
<body>
<main class="canvas">
  <section class="business-card" aria-label="Corvane Construction business card">
    <svg class="card-art" viewBox="0 0 940 537" preserveAspectRatio="none" aria-hidden="true">
      <defs>
        <linearGradient id="frostShade" x1="0" y1="0" x2="1" y2="1">
          <stop offset="0" stop-color="#f7f6f5"/>
          <stop offset="1" stop-color="#e2dfdd"/>
        </linearGradient>
        <linearGradient id="maroonShade" x1="0" y1="0" x2="1" y2="1">
          <stop offset="0" stop-color="#5f2029"/>
          <stop offset="1" stop-color="#4a1720"/>
        </linearGradient>
      </defs>
      <rect class="frost-panel" x="0" y="0" width="940" height="537" fill="url(#frostShade)"/>
      <path class="maroon-panel" role="img" aria-label="Textured maroon stone surface"
            d="M90 0 H940 V537 H250 C400 470 560 330 672 270 C560 230 380 90 90 0 Z"
            fill="url(#maroonShade)"/>
    </svg>

    <div class="brand-name">
      <span class="brand-main">CORVANE</span>
      <span class="brand-sub">CONSTRUCTION</span>
    </div>

    <div class="holder">
      <p class="holder-name">DWAYNE HALSTER</p>
      <p class="holder-role">Owner</p>
    </div>

    <address class="contact">
      4875 FM 309<br>
      Ardell, NM 87412<br>
      (505) 482-5096
    </address>
  </section>
</main>
</body>
</html>
```